Money Mindset Podcast needs fun, creative cover art

Launching a new podcast called 'Turning Your Thoughts Toward Savings' - aimed at an audience 30-50 who are interested in the practicalities of managing their money but also the more mental and emotional aspects.
Looking for something not too serious, warm and friendly.

Must be easy to read on phone screens
3000 x 3000 in size
Avoid currency symbols $, £ etc, as may have an international audience

Target Market(s)

Podcast listeners age 30-50 starting in the UK but then worldwide. Probably 60:40 female bias

Industry/Entity Type

Life Coaching

Font styles to use
Serif
Sans Serif

Colors
cadf82
fee18a
acd037
85cae6
eea4c8
f59195
85acd3

Requirements
Must have
• Simple, clear design. Easy to read on variety of devices. 3000 x 3000
Appeal to those with a spiritual or emotional interests
Nice to have
• Stand out among other money related podcasts
Maybe play around with clouds, lightbulbs and clearing skies
Should not have
• Currency symbols such as $ or £
Be too corporate or bank like
Stock images

```html
<!DOCTYPE html>
<html lang="en">
<head>
<meta charset="utf-8">
<title>Money Mindset Podcast – Cover Art Samples</title>
<link rel="stylesheet" href="https://fonts.googleapis.com/css2?family=Montserrat:wght@400;800&family=Oswald:wght@300;400&display=swap">
<style>
  :root {
    --sheet-bg: #1e1e1e;
    --header-bg: #000000;
    --label: #e6e6e6;
    --ink-dark: #272324;
    --ink-charcoal: #323232;
    --ink-black: #0d0d0d;
    --ink-brown: #2e1f1f;
    --white: #ffffff;
    --lime: #acd037;
    --sky: #85cae6;
    --pink: #f59195;
    --yellow: #fee18a;
    --blue: #85acd3;
    --cloud-deep: #3f6fb0;
    --cloud-mid: #9fb9d6;
    --cloud-light: #eef2f6;
  }
  * { box-sizing: border-box; margin: 0; padding: 0; }
  html, body { width: 1200px; height: 2244px; overflow: hidden; }
  body {
    position: relative;
    background: var(--sheet-bg);
    font-family: "Oswald", "Arial Narrow", sans-serif;
  }
  .sheet-header {
    position: absolute; left: 0; top: 0;
    width: 1200px; height: 118px;
    background: var(--header-bg);
    display: flex; align-items: center; justify-content: center;
  }
  .sheet-title {
    font-family: "Montserrat", Arial, sans-serif;
    font-weight: 400;
    font-size: 26px;
    letter-spacing: 13px;
    color: var(--white);
  }
  .sample-label {
    position: absolute; left: 47px;
    font-family: "Montserrat", Arial, sans-serif;
    font-size: 16px; letter-spacing: 6px;
    color: var(--label);
  }
  .cover {
    position: absolute; left: 47px;
    width: 548px; height: 548px;
    overflow: hidden;
  }
  .cover-art { position: absolute; inset: 0; width: 100%; height: 100%; }
  .cover-title {
    position: absolute;
    text-align: right;
    text-transform: uppercase;
    line-height: 0.98;
  }
  .title-lead {
    display: block;
    font-family: "Oswald", "Arial Narrow", sans-serif;
    font-weight: 300;
    color: var(--white);
  }
  .title-strong {
    display: block;
    font-family: "Montserrat", Arial, sans-serif;
    font-weight: 800;
    color: var(--lime);
    letter-spacing: -0.04em;
  }
  .title-strong.is-big { line-height: 0.9; }
  .title-strong.is-long { line-height: 1; letter-spacing: -0.045em; }
  .title-tail {
    display: block;
    font-family: "Oswald", "Arial Narrow", sans-serif;
    font-weight: 400;
    color: var(--white);
  }
  .title-tail .accent { color: var(--sky); }

  /* Sample 1 – paper layers */
  .cover--paper { top: 216px; background: var(--ink-dark); }
  .cover--paper .cover-title { right: 46px; top: 46px; }
  .cover--paper .title-lead { font-size: 54px; letter-spacing: 14px; margin-right: -14px; }
  .cover--paper .title-strong.is-big { font-size: 112px; }
  .cover--paper .title-strong.is-long { font-size: 62px; }
  .cover--paper .title-tail { font-size: 56px; }

  /* Sample 2 – stacked stripes */
  .cover--stripes { top: 928px; background: var(--ink-charcoal); }
  .cover--stripes .cover-title { right: 32px; top: 58px; }
  .cover--stripes .title-lead { font-size: 68px; }
  .cover--stripes .title-strong.is-big { font-size: 110px; }
  .cover--stripes .title-strong.is-long { font-size: 64px; }
  .cover--stripes .title-tail { font-size: 54px; }

  /* Sample 3 – open sky */
  .cover--sky { top: 1631px; background: var(--ink-black); }
  .cover--sky .cover-title { right: 32px; top: 78px; }
  .cover--sky .title-lead { font-size: 70px; }
  .cover--sky .title-strong.is-big { font-size: 112px; }
  .cover--sky .title-strong.is-long { font-size: 68px; }
  .cover--sky .title-tail { font-size: 58px; }
  .cover--sky .title-strong,
  .cover--sky .title-tail .accent { color: var(--white); }
</style>
</head>
<body>

<header class="sheet-header">
  <h1 class="sheet-title">MONEY MINDSET PODCAST _3000 X 3000</h1>
</header>

<p class="sample-label" style="top:178px">SAMPLE 1</p>
<section class="cover cover--paper">
  <svg class="cover-art" viewBox="0 0 548 548" role="img" aria-label="Paper-cut head silhouette in profile, layered in pink and green on the left side">
    <rect width="548" height="548" fill="var(--pink)"/>
    <g id="paper-head">
      <path transform="translate(-20 22)" fill="var(--lime)" d="M52 -40 H620 V620 H478 C458 540 420 460 372 462 C320 466 280 500 244 452 C214 410 196 372 178 318 C166 262 140 212 112 160 C84 108 60 50 52 -40 Z"/>
      <path fill="var(--ink-dark)" d="M52 -40 H620 V620 H478 C458 540 420 460 372 462 C320 466 280 500 244 452 C214 410 196 372 178 318 C166 262 140 212 112 160 C84 108 60 50 52 -40 Z"/>
    </g>
  </svg>
  <h2 class="cover-title">
    <span class="title-lead">Turning</span>
    <span class="title-strong is-big">Your</span>
    <span class="title-strong is-long">Thoughts</span>
    <span class="title-tail">Toward <span class="accent">Savings</span></span>
  </h2>
</section>

<p class="sample-label" style="top:884px">SAMPLE 2</p>
<section class="cover cover--stripes">
  <svg class="cover-art" viewBox="0 0 548 548" role="img" aria-label="Three stacked head silhouettes in profile in blue, yellow and pink">
    <rect width="548" height="548" fill="var(--blue)"/>
    <path transform="translate(-96 0)" fill="var(--yellow)" d="M197 -10 H640 V600 H330 C300 530 240 500 206 462 C176 426 166 386 170 336 C174 286 146 240 154 186 C164 122 200 60 197 -10 Z"/>
    <path transform="translate(-48 0)" fill="var(--pink)" d="M197 -10 H640 V600 H330 C300 530 240 500 206 462 C176 426 166 386 170 336 C174 286 146 240 154 186 C164 122 200 60 197 -10 Z"/>
    <path fill="var(--ink-charcoal)" d="M197 -10 H640 V600 H330 C300 530 240 500 206 462 C176 426 166 386 170 336 C174 286 146 240 154 186 C164 122 200 60 197 -10 Z"/>
  </svg>
  <h2 class="cover-title">
    <span class="title-lead">Turning</span>
    <span class="title-strong is-big">Your</span>
    <span class="title-strong is-long">Thoughts</span>
    <span class="title-tail">Toward <span class="accent">Savings</span></span>
  </h2>
</section>

<p class="sample-label" style="top:1592px">SAMPLE 3</p>
<section class="cover cover--sky">
  <svg class="cover-art" viewBox="0 0 548 548" role="img" aria-label="Head silhouette in profile filled with a photograph of white clouds in a blue sky, edged in dark brown on black">
    <defs>
      <linearGradient id="sky-fill" x1="0" y1="0" x2="0.4" y2="1">
        <stop offset="0" stop-color="var(--cloud-light)"/>
        <stop offset="0.35" stop-color="var(--cloud-mid)"/>
        <stop offset="0.7" stop-color="var(--cloud-deep)"/>
        <stop offset="1" stop-color="var(--cloud-light)"/>
      </linearGradient>
    </defs>
    <rect width="548" height="548" fill="var(--ink-black)"/>
    <path transform="translate(-24 10)" fill="var(--ink-brown)" d="M140 -20 H640 V620 H275 C240 560 150 520 120 480 C90 440 72 384 80 332 C88 282 54 240 62 190 C72 120 120 60 140 -20 Z"/>
    <path fill="url(#sky-fill)" d="M140 -20 H640 V620 H275 C240 560 150 520 120 480 C90 440 72 384 80 332 C88 282 54 240 62 190 C72 120 120 60 140 -20 Z"/>
  </svg>
  <h2 class="cover-title">
    <span class="title-lead">Turning</span>
    <span class="title-strong is-big">Your</span>
    <span class="title-strong is-long">Thoughts</span>
    <span class="title-tail">Toward <span class="accent">Savings</span></span>
  </h2>
</section>

</body>
</html>
```